Executive Business Card for Healthcare Company [Need Today]

I need a business card design for a healthcare company. The only branding the company has thus far is a logo. The cards will be utilized by company executives. The design I envision will be vibrant and appealing but with a corporate feel. They shouldn't be too casual or playful. I would like to complete this project TODAY if possible.

Target Market(s)

Healthcare vendors, other executives in healthcare and pharmaceuticals

Industry/Entity Type

Pharmaceutical

Contact Information for Business Card

See attachment

Font styles to use
Serif
Sans Serif

Colors

Designer to choose colors to be used in the design.

```html
<!DOCTYPE html>
<html lang="en">
<head>
<meta charset="utf-8">
<title>Corvela Therapeutics – Business Card</title>
<link rel="stylesheet" href="https://fonts.googleapis.com/css2?family=Roboto:wght@300;400;500&display=swap">
<style>
  :root {
    --backdrop: #3b3b3d;
    --card: #1e1e20;
    --teal: #29b6c6;
    --ring: #3db89a;
    --ink: #e9e9ea;
    --muted: #c9c9cb;
  }
  * { margin: 0; padding: 0; box-sizing: border-box; }
  html, body {
    width: 799px; height: 1200px; overflow: hidden;
    background: var(--backdrop);
    font-family: "Roboto", sans-serif;
  }
  .sheet {
    position: relative; width: 799px; height: 1200px;
    display: flex; flex-direction: column; align-items: center; justify-content: space-around;
    padding: 60px 0;
  }
  .card {
    position: relative; width: 660px; height: 377px;
    background: var(--card);
    border-radius: 3px;
    box-shadow: 0 14px 30px rgba(0,0,0,.45);
  }
  .brand-ring {
    position: absolute; border: 4px solid var(--ring); border-radius: 50%;
  }
  .brand-name {
    position: absolute; color: var(--teal); font-weight: 400; line-height: 1.05;
  }
  .brand-name .line { display: block; }

  /* Front */
  .card-front .brand-ring { left: 150px; top: 108px; width: 110px; height: 110px; }
  .card-front .divider {
    position: absolute; left: 282px; top: 122px; width: 2px; height: 84px; background: var(--muted);
  }
  .card-front .brand-name { left: 304px; top: 120px; font-size: 40px; }
  .card-front .brand-name .sub { font-size: 28px; font-weight: 400; }
  .card-front .website {
    position: absolute; left: 0; right: 0; top: 270px; text-align: center;
    color: var(--ink); font-size: 17px; letter-spacing: 3px; font-weight: 300;
  }

  /* Back */
  .card-back .brand-ring { left: 118px; top: 70px; width: 100px; height: 100px; }
  .card-back .brand-name { left: 66px; top: 188px; font-size: 36px; }
  .card-back .brand-name .sub { font-size: 26px; }
  .contact { position: absolute; left: 390px; top: 112px; color: var(--ink); }
  .contact .person { color: var(--teal); font-size: 28px; font-weight: 500; }
  .contact .role { font-size: 14px; color: var(--muted); margin: 4px 0 18px; }
  .contact ul { list-style: none; font-size: 17px; line-height: 24px; }
  .contact li { display: flex; align-items: center; gap: 8px; }
  .contact li svg { width: 14px; height: 14px; flex: none; }
  .contact .address { font-size: 17px; line-height: 24px; margin-top: 2px; }
</style>
</head>
<body>
<main class="sheet">
  <section class="card card-front">
    <span class="brand-ring"></span>
    <span class="divider"></span>
    <p class="brand-name"><span class="line">corvela</span><span class="line sub">therapeutics</span></p>
    <p class="website">www.corvelarx.com</p>
  </section>

  <section class="card card-back">
    <span class="brand-ring"></span>
    <p class="brand-name"><span class="line">corvela</span><span class="line sub">therapeutics</span></p>
    <div class="contact">
      <p class="person">Daniel Marsh</p>
      <p class="role">Senior Director of Marketing</p>
      <ul>
        <li>
          <svg viewBox="0 0 16 16" aria-hidden="true"><path fill="var(--teal)" d="M3 1l3 3-1.5 2a9 9 0 0 0 5.5 5.5L12 10l3 3-2 2C7 15 1 9 1 3z"/></svg>
          555-201-4837
        </li>
        <li>
          <svg viewBox="0 0 16 16" aria-hidden="true"><rect x="4" y="1" width="8" height="14" rx="1.5" fill="var(--teal)"/><rect x="5.5" y="3" width="5" height="8" fill="var(--card)"/></svg>
          555-319-6024
        </li>
        <li>
          <svg viewBox="0 0 16 16" aria-hidden="true"><circle cx="8" cy="8" r="7" fill="var(--teal)"/><path d="M1 8h14M8 1c3 3 3 11 0 14M8 1c-3 3-3 11 0 14" stroke="var(--card)" stroke-width="1" fill="none"/></svg>
          dmarsh@corvelarx.com
        </li>
      </ul>
      <p class="address">118 Linden Park Avenue<br>Riverton, GA 30190</p>
    </div>
  </section>
</main>
</body>
</html>
```